Card Design Project

A simple, funky, cool birth announcement card
Not corporate, but arty
Not childish nor girlish
No baby pictures

Text is tbc (eg name and date may change)

Front side: just the name "fenna"
Should be easy to read

Back side text (in Dutch):

We vinden je nu al leuk!

20 JUNE 2013
Singapore

Dochter van Marieke Dorrel & Joost Vermalen

Yangon, Myanmar
+95 1 64 8319
Skype: Marieke.Dorrel
Skype: Joost.Vermalen

Size will be A6
Updates

Reason: Dear designers, At this stage we would like to have one or more designers to draft up the card (of which the final text is still tbd as the baby is yet to be born) using the typeface used on the left below (or similar!) of the newly added picture - in black - in fluorescent colours Can you get back to us in a few days? Thanks

Target Market(s)

Our funky friends in holland.

Industry/Entity Type

Baby

Requirements
Must have
• Colours, aswe are very happy to welcome this baby.
Something that makes it stand out from all other baby birth announcement cards

A6 size
Deadline 21 June
Printing will be on white (thick paper 250g)
Design for 5mm "bleedsides" all around
At least available in PDF (and other formats)
Nice to have
• We've recently moved from netherlands to Yangon
We could include the iconic kyauktaran pagoda

I would like for it to look like a cool party announcement

Include bright fluoriscent colours, including orange.
The enveloppe will be orange
Should not have
• Any baby stuff, soft pink dominance, childish stuff.

```html
<!DOCTYPE html>
<html lang="nl">
<head>
<meta charset="utf-8">
<title>Fenna – geboortekaart</title>
<link rel="stylesheet" href="https://fonts.googleapis.com/css2?family=Federo&family=Passion+One:wght@700&display=swap">
<style>
  :root {
    --ink: #0b0a09;
    --panel: #100e0c;
    --cream: #f6ecd2;
    --name-fill: #fbefd8;
    --name-edge: #e2531d;
    --paint-red: #c3301f;
    --paint-orange: #e8762a;
    --paint-green: #2f6a2b;
    --paint-dark: #3a1d14;
    --gold: #e3a526;
    --night: #050403;
  }
  * { margin: 0; padding: 0; box-sizing: border-box; }
  html, body { width: 1200px; height: 866px; overflow: hidden; background: var(--ink); }
  .card { position: relative; width: 1200px; height: 866px; background: var(--panel); overflow: hidden; }

  .paint-band { position: absolute; left: 0; width: 640px; }
  .paint-band--top {
    top: 0; height: 98px;
    background: linear-gradient(100deg, var(--paint-green) 0%, var(--paint-red) 22%, var(--paint-orange) 40%, var(--paint-dark) 58%, var(--paint-green) 76%, var(--paint-red) 100%);
  }
  .paint-band--bottom {
    top: 680px; height: 186px;
    background: linear-gradient(95deg, var(--paint-dark) 0%, var(--paint-green) 20%, var(--paint-red) 42%, var(--paint-orange) 62%, var(--paint-green) 80%, var(--paint-red) 100%);
  }
  .shade-band { position: absolute; left: 640px; width: 560px; opacity: .5; }
  .shade-band--top { top: 0; height: 98px; background: linear-gradient(90deg, #2a1810, #1a120c 50%, #24140e); }
  .shade-band--bottom { top: 680px; height: 186px; background: linear-gradient(90deg, #1f150f, #2c1a12 40%, #181210); }

  .night-photo {
    position: absolute; left: 0; top: 98px; width: 640px; height: 582px;
    background: radial-gradient(ellipse 140px 190px at 355px 300px, var(--gold) 0%, #8a5a12 45%, transparent 80%),
                linear-gradient(180deg, #0d0b08 0%, #0a0907 55%, var(--night) 100%);
  }

  .back-text {
    position: absolute; left: 700px; top: 0;
    font-family: "Federo", sans-serif; font-size: 27px; letter-spacing: 2px;
    color: var(--cream); text-transform: uppercase; line-height: 40px;
  }
  .line { position: absolute; left: 0; white-space: nowrap; }
  .greeting { top: 122px; }
  .birth-date { top: 198px; }
  .birth-place { top: 240px; }
  .parents-intro { top: 356px; }
  .parent--mother { top: 398px; left: 70px; }
  .parent--father { top: 438px; left: 140px; }
  .home-city { top: 594px; }
  .phone { top: 636px; }
  .skype--mother { top: 676px; }
  .skype--father { top: 716px; }

  .baby-name {
    position: absolute; left: 200px; top: 680px;
    font-family: "Passion One", sans-serif; font-weight: 700; font-size: 128px;
    color: var(--name-fill); -webkit-text-stroke: 3px var(--name-edge);
    letter-spacing: 2px; transform: rotate(-4deg); transform-origin: left bottom;
    line-height: 1;
  }
</style>
</head>
<body>
<main class="card">
  <div class="paint-band paint-band--top" role="img" aria-label="Painted fluorescent texture in red, orange and green"></div>
  <div class="shade-band shade-band--top"></div>
  <div class="night-photo" role="img" aria-label="Night photograph of the golden kyauktaran pagoda lit above the Yangon skyline"></div>
  <div class="paint-band paint-band--bottom" role="img" aria-label="Painted fluorescent texture in red, orange and green"></div>
  <div class="shade-band shade-band--bottom"></div>

  <section class="back-text">
    <p class="line greeting">We vinden je nu al leuk!</p>
    <p class="line birth-date">20 June 2013</p>
    <p class="line birth-place">Singapore</p>
    <p class="line parents-intro">Dochter van</p>
    <p class="line parent--mother">Marieke Dorrel &amp;</p>
    <p class="line parent--father">Joost Vermalen</p>
    <p class="line home-city">Yangon, Myanmar</p>
    <p class="line phone">+95 1 64 8319</p>
    <p class="line skype--mother">Skype: Marieke.Dorrel</p>
    <p class="line skype--father">Skype: Joost.Vermalen</p>
  </section>

  <h1 class="baby-name">FENNA</h1>
</main>
</body>
</html>
```